deceased estate clean ups brochures

we would like a brochure to reresent our business we already have new web site and want to do DL A4 brochure to give out to promote our business we already have logo www.brightmoor.com.au is where you can get all info needed

Target Market(s)

families with loved ones that have past away
people done sizing or needing to decluter

Colors
cadf82
33b8a4
886aae
33a6d7

```html
<!DOCTYPE html>
<html lang="en">
<head>
<meta charset="utf-8">
<title>Brightmoor – DL Brochure</title>
<link href="https://fonts.googleapis.com/css2?family=Montserrat:wght@500;600;700&family=Open+Sans:wght@400;600;700&family=Cinzel:wght@500;600&display=swap" rel="stylesheet">
<style>
:root{
  --green:#2f9a3c;
  --green-dark:#1d7a2c;
  --green-light:#8cc63f;
  --ink:#2d2d2d;
  --body:#555;
  --panel-top:#ffffff;
  --panel-grey:#dcdcdc;
  --canvas:#efefef;
}
*{box-sizing:border-box;margin:0;padding:0}
html,body{width:1200px;height:1200px;overflow:hidden;background:var(--canvas)}
body{font-family:"Open Sans",Arial,sans-serif;color:var(--body);position:relative}
.spread{position:absolute;left:200px;width:800px;height:566px;display:flex;box-shadow:0 2px 10px rgba(0,0,0,.15);background:#fff}
.spread--outside{top:22px}
.spread--inside{top:612px}
.panel{position:relative;width:266.67px;height:100%;overflow:hidden}
.panel--grey{background:linear-gradient(180deg,var(--panel-top) 0%,var(--panel-grey) 100%)}
.panel--cover{background:linear-gradient(180deg,#e6e6e6 0%,#cfcfcf 100%)}
.heading{font-family:"Montserrat",Arial,sans-serif;font-weight:700;color:var(--green);text-transform:uppercase;letter-spacing:.5px}
.feature{display:flex;gap:6px;margin-bottom:9px}
.feature__icon,.service__icon{flex:none;width:12px;height:12px;border-radius:50%;background:var(--green);margin-top:2px}
.feature__title{font-family:"Montserrat",Arial,sans-serif;font-weight:700;font-size:10px;color:var(--ink);margin-bottom:2px}
.small{font-size:6px;line-height:1.45}
.small b{color:var(--ink)}
.brand{font-family:"Cinzel",serif;font-weight:600;color:var(--ink);letter-spacing:1.5px;display:flex;align-items:center;gap:5px}
.brand__dot{width:9px;height:9px;border-radius:50%;background:var(--green)}
.photo{position:absolute}
.goal{font-family:"Cinzel",serif;font-weight:500;color:var(--ink);text-align:center;line-height:1.05}
.goal em{font-style:normal;color:var(--green);font-weight:600}
.service{margin-bottom:7px}
.service__head{display:flex;gap:5px;align-items:flex-start;font-family:"Montserrat",Arial,sans-serif;font-weight:600;font-size:9.5px;color:var(--ink);text-transform:uppercase;line-height:1.15;margin-bottom:3px}
.service__head--sentence{text-transform:none}
.ticks{list-style:none;font-size:5.6px;line-height:1.35}
.ticks li{position:relative;padding-left:9px;margin-bottom:2px}
.ticks li::before{content:"";position:absolute;left:0;top:1px;width:4px;height:4px;border:1px solid var(--green);border-radius:50%}
.ticks--2col{display:grid;grid-template-columns:1fr 1fr;column-gap:6px}
.contact{list-style:none;font-size:6.5px;color:var(--ink);line-height:1.3}
.contact li{display:flex;gap:5px;align-items:flex-start;margin-bottom:3px}
.contact svg{flex:none;margin-top:1px}
</style>
</head>
<body>

<!-- OUTSIDE SPREAD -->
<section class="spread spread--outside">

  <div class="panel panel--grey" style="padding:20px 14px 0 14px">
    <h2 class="heading" style="font-size:15px;margin-bottom:12px">Why choose us</h2>
    <div class="feature"><span class="feature__icon"></span><div>
      <p class="feature__title">Quality</p>
      <p class="small">Our aim is to lift your property and earn the trust you place in us, delivering quality work that meets every expectation.</p></div></div>
    <div class="feature"><span class="feature__icon"></span><div>
      <p class="feature__title">Pride</p>
      <p class="small">We take pride in our family approach and care. Whether it is simple cleaning, house repairs or larger renovations, your home will be ready for rental or sale.</p></div></div>
    <div class="feature"><span class="feature__icon"></span><div>
      <p class="feature__title">Professionalism</p>
      <p class="small">Brightmoor only uses quality staff and materials that are <b>"fit for purpose"</b>. We take a professional approach to every job, ensuring all agreed tasks are completed and accounted for.</p></div></div>
    <div class="feature"><span class="feature__icon"></span><div>
      <p class="feature__title">Areas Serviced</p>
      <p class="small"><b>Specialising in Melbourne CBD and suburbs including:</b></p>
      <p class="small" style="margin-top:4px">Northgate, Elmwood, Brookfield, Hillcrest, Riverside, Oakdale, Fernvale, Westbury</p>
      <p class="small" style="margin-top:4px">Kingsley, Ashford, Greenhill, Maple Park, Lakeside, Southbank</p>
      <p class="small" style="margin-top:4px">Pinewood, Stonebridge, Ridgeview, Harbourside, Clearwater</p>
      <p class="small" style="margin-top:4px">Bayview, Millbrook, Glenfield</p></div></div>
    <p class="small" style="color:var(--green-dark);font-weight:700">If you're not sure we service your area, give us a call.</p>
    <div class="brand" style="position:absolute;right:16px;bottom:92px;font-size:8px"><span class="brand__dot"></span>BRIGHTMOOR</div>
    <div class="photo" role="img" aria-label="Photo of cleaning bottles, sponges and cloths in a green bucket" style="left:0;bottom:0;width:100%;height:82px;background:linear-gradient(90deg,#6fb7d8 0%,#8cc63f 45%,#f3c96a 75%,#e9e4dc 100%)"></div>
  </div>

  <div class="panel panel--grey" style="padding:0 16px">
    <svg width="266" height="120" style="position:absolute;left:0;top:0" aria-hidden="true"><circle cx="150" cy="20" r="72" fill="none" stroke="#d5d5d5" stroke-width="6"/></svg>
    <h2 class="heading" style="position:absolute;top:330px;left:16px;font-size:21px;line-height:1;color:var(--green)">Call us<br>now</h2>
    <p style="position:absolute;top:384px;left:16px;font-family:'Montserrat',sans-serif;font-weight:700;font-size:18px;color:var(--ink);letter-spacing:.5px">0400 318 726</p>
    <p style="position:absolute;top:420px;left:16px;font-family:'Montserrat',sans-serif;font-weight:600;font-size:12px;color:var(--ink)">Contact Details</p>
    <ul class="contact" style="position:absolute;top:442px;left:16px">
      <li><svg width="7" height="8" viewBox="0 0 10 12"><path d="M5 0a4 4 0 0 1 4 4c0 3-4 8-4 8S1 7 1 4a4 4 0 0 1 4-4z" fill="#2d2d2d"/></svg>PO Box 210,<br>Northgate 3099</li>
      <li><svg width="7" height="7" viewBox="0 0 10 10"><circle cx="5" cy="5" r="5" fill="#2d2d2d"/><path d="M3 3l1 0 1 2-1 1 1 1 1-1 2 1v1a5 5 0 0 1-5-5z" fill="#fff"/></svg>0400 318 726</li>
      <li><svg width="7" height="7" viewBox="0 0 10 10"><circle cx="5" cy="5" r="5" fill="#2d2d2d"/><rect x="2.5" y="3.3" width="5" height="3.4" fill="none" stroke="#fff" stroke-width=".8"/></svg>info@brightmoor.com.au</li>
      <li><svg width="7" height="7" viewBox="0 0 10 10"><circle cx="5" cy="5" r="5" fill="#2d2d2d"/><circle cx="5" cy="5" r="2.6" fill="none" stroke="#fff" stroke-width=".8"/></svg>www.brightmoor.com.au</li>
    </ul>
  </div>

  <div class="panel panel--cover">
    <div class="brand" style="position:absolute;top:56px;left:0;width:100%;justify-content:center;font-size:12px"><span class="brand__dot"></span>BRIGHTMOOR</div>
    <svg width="267" height="260" style="position:absolute;left:0;top:98px" aria-hidden="true">
      <defs><linearGradient id="swooshA" x1="0" y1="0" x2="1" y2="1"><stop offset="0" stop-color="#8cc63f"/><stop offset="1" stop-color="#1d7a2c"/></linearGradient></defs>
      <circle cx="140" cy="124" r="112" fill="url(#swooshA)"/>
      <circle cx="128" cy="136" r="104" fill="#e9e9e9"/>
      <circle cx="132" cy="130" r="92" fill="#fff"/>
    </svg>
    <div class="photo" role="img" aria-label="Photo of two cleaners wiping a glass table and mopping a bright living room" style="left:46px;top:142px;width:172px;height:172px;border-radius:50%;background:radial-gradient(circle at 45% 40%,#f4f1ec 0%,#d9d3ca 55%,#a8a097 100%)"></div>
    <p class="goal" style="position:absolute;top:418px;left:0;width:100%;font-size:21px">AT <em>BRIGHTMOOR</em><br>IS OUR <em>GOAL</em></p>
    <p class="small" style="position:absolute;top:476px;left:26px;right:26px;text-align:center;color:var(--ink)">Welcome to Brightmoor, a company that cares solely about your best interest and the care for the estate of your loved one.</p>
  </div>
</section>

<!-- INSIDE SPREAD -->
<section class="spread spread--inside">

  <div class="panel panel--grey">
    <svg width="267" height="260" style="position:absolute;left:0;top:0" aria-hidden="true">
      <defs><linearGradient id="swooshB" x1="0" y1="0" x2="1" y2="1"><stop offset="0" stop-color="#1d7a2c"/><stop offset="1" stop-color="#8cc63f"/></linearGradient></defs>
      <circle cx="140" cy="70" r="168" fill="url(#swooshB)"/>
      <circle cx="160" cy="58" r="158" fill="#f3f3f3"/>
      <circle cx="163" cy="55" r="148" fill="#fff"/>
    </svg>
    <div class="photo" role="img" aria-label="Photo of a gloved hand planting seedlings in a garden bed" style="left:24px;top:-86px;width:280px;height:280px;border-radius:50%;background:radial-gradient(circle at 60% 65%,#7fb34a 0%,#3f7d2a 55%,#284f1d 100%)"></div>
    <div style="position:absolute;top:290px;left:14px;right:14px">
      <h2 class="heading" style="font-size:15px;margin-bottom:10px">About our company</h2>
      <p class="small" style="margin-bottom:6px">At <b style="color:var(--green)">Brightmoor</b> our goal is to ease your worries and help you with your journey in preparing your house for rental or resale.</p>
      <p class="small" style="margin-bottom:6px">Whether it is a move to another residence or the difficult task of dealing with the grief when a loved one passes away, <b style="color:var(--green)">Brightmoor</b> can help with the preparation of the property for sale. <b style="color:var(--green)">Brightmoor</b> will come in, remove unwanted items and dispose of all rubbish, do cosmetic repairs if required and leave the property in a spotless state.</p>
      <p class="small" style="margin-bottom:6px">Our trained and reliable staff repair any house and carry out landscaping in preparation for renting or resale of the property in a timely and professional manner. Our team provides a discreet and trustworthy service, keeping in mind the sensitive nature of the work.</p>
      <p class="small"><b style="color:var(--green)">Brightmoor</b> will make sure that all remaining furniture and possessions left inside the property are removed, sold or taken to storage and the remainder of unwanted goods are sorted so that the entire property is completely cleared for rental or sale.</p>
    </div>
  </div>

  <div class="panel" style="background:linear-gradient(180deg,#fff 0%,#e4e4e4 100%)">
    <div class="photo" role="img" aria-label="Photo of two removalists in blue caps loading boxes into a van" style="left:0;top:0;width:533px;height:170px;background:linear-gradient(180deg,rgba(160,180,205,.9) 0%,rgba(205,215,228,.8) 55%,rgba(255,255,255,0) 100%)"></div>
    <div style="position:absolute;top:168px;left:14px;right:12px">
      <h2 class="heading" style="font-size:14px;margin-bottom:8px">Services offered</h2>
      <div class="service">
        <p class="service__head service__head--sentence"><span class="service__icon"></span>Senior / Aged care relocations and down sizing</p>
        <p class="small" style="padding-left:17px;margin-bottom:3px"><b>That's where Brightmoor can help you. Our removal and home relocation services include:</b></p>
        <ul class="ticks" style="padding-left:17px">
          <li>Decluttering and sorting your belongings</li>
          <li>Packing, moving and unpacking into your new home</li>
          <li>Delivering your unwanted goods to various charities</li>
          <li>Removing all items deemed rubbish</li>
          <li>Preparing your home for rental or sale</li>
        </ul>
      </div>
      <div class="service">
        <p class="service__head"><span class="service__icon"></span>Deceased estates</p>
        <p class="small" style="padding-left:17px;margin-bottom:3px"><b>Our experienced staff can provide comprehensive services:</b></p>
        <ul class="ticks" style="padding-left:17px">
          <li>House clearing</li>
          <li>Preparation for sale</li>
          <li>Cosmetic repairs and house maintenance</li>
        </ul>
      </div>
      <div class="service">
        <p class="service__head"><span class="service__icon"></span>Cleaning service</p>
        <p class="small" style="padding-left:17px;margin-bottom:3px"><b>We guarantee the property will be left in a perfect condition for renting or sale</b></p>
        <ul class="ticks ticks--2col" style="padding-left:17px">
          <li>Cleaning of walls, floors and ceilings</li>
          <li>Shed and garage cleaning</li>
          <li>Window cleaning</li>
          <li>Rubbish removal</li>
          <li>Bathrooms, kitchens and living spaces</li>
          <li>Gardening / landscaping</li>
          <li>Packing of delicate and personal items</li>
          <li>All maintenance repairs</li>
          <li>Steam cleaning</li>
          <li>Interior decorating</li>
        </ul>
      </div>
    </div>
  </div>

  <div class="panel" style="background:linear-gradient(180deg,rgba(255,255,255,0) 0%,#fff 32%,#fafafa 100%)">
    <svg width="267" height="140" style="position:absolute;left:0;bottom:0" aria-hidden="true"><circle cx="250" cy="130" r="68" fill="none" stroke="#e2e2e2" stroke-width="6"/></svg>
    <div style="position:absolute;top:126px;left:14px;right:14px">
      <div class="service">
        <p class="service__head"><span class="service__icon"></span>Cosmetic repairs and<br>house maintenance</p>
        <p class="small" style="padding-left:17px;margin-bottom:3px"><b>Common additional services requested by our customers include:</b></p>
        <ul class="ticks ticks--2col" style="padding-left:17px">
          <li>Painting</li>
          <li>Garden maintenance and landscaping</li>
          <li>New carpets or floorboards</li>
          <li>Fencing</li>
          <li>House repairs – plastering, electrical, plumbing (by licensed tradespeople)</li>
          <li>Brickwork</li>
          <li>Bathroom and kitchen renovations</li>
          <li>Decking</li>
        </ul>
      </div>
      <div class="service" style="margin-top:8px">
        <p class="service__head"><span class="service__icon"></span>Preparation for rental<br>or sale</p>
        <div class="small" style="padding-left:17px">
          <p style="margin-bottom:3px"><b>Common additional services requested by our customers include:</b></p>
          <p style="margin-bottom:3px">Our target is to create maximum appeal on all aspects of your property, allowing you to set or rent and attract a higher sale price when properly prepared and presented.</p>
          <p style="margin-bottom:3px">We can advise you whether you need to make any cosmetic updates or repairs to improve your home's resale value.</p>
          <p>We can do cosmetic renovations, clean and declutter your entire home from top to bottom. We will leave you with a clean, tidy and market ready house ready to sell, rent or move into.</p>
        </div>
      </div>
      <div class="service" style="margin-top:8px">
        <p class="service__head"><span class="service__icon"></span>Garden makeovers</p>
        <p class="small" style="padding-left:17px;margin-bottom:3px">We offer all services including:</p>
        <ul class="ticks ticks--2col" style="padding-left:17px">
          <li>Planting</li><li>Brickwork</li>
          <li>Concreting</li><li>Pergolas</li>
          <li>Paving</li><li>Maintenance</li>
          <li>Fencing</li><li>Grass or synthetic lawns</li>
          <li>Decking</li>
        </ul>
      </div>
    </div>
  </div>
</section>

</body>
</html>
```